Law Firm Business Card

This is a business card for a law firm that serves US military and veterans.

The card must have ONLY the following (we want an uncluttered look):

- Company logo (PNG, GIF, JPEG copies uploaded)
- A tagline reading: "a law firm for service members and veterans"
- My name and title: "Tobias Marlow" and "Attorney"
- My email: "tobias.marlow@brinmoorlegal.com"
- My number: "855-FIRM-ONE (347-6663)"

We are looking for a clean, simple layout with only the above information, likely printed on a bright white cotton stock. The font of our logo is DIN 1451, and the font used on our website is Helvetica Neue. The color of our logo is #336699, and we probably want the tagline in that color also, and my contact information in a dark grey. Please review our website at www.brinmoorlegal.com to ensure your card design complements our website style.

Thanks and we look forward to seeing your submissions.

A few notes:

- Two-sided submissions are ok
- Please don't add graphics (scales of justice, judges hammer, etc)

```html
<!DOCTYPE html>
<html lang="en">
<head>
<meta charset="utf-8">
<title>Brinmoor Legal – Business Card</title>
<link rel="stylesheet" href="https://fonts.googleapis.com/css2?family=Tinos:wght@400;700&display=swap">
<style>
  :root {
    --brand-blue: #2667cc;
    --deep-blue: #0b2fa8;
    --paper: #ffffff;
    --ink: #333333;
    --stage: #e9e9ec;
    --rule: #cfcfcf;
  }
  * { margin: 0; padding: 0; box-sizing: border-box; }
  html, body {
    width: 1200px; height: 961px; overflow: hidden;
    background: var(--stage);
  }
  .stage {
    width: 1200px; height: 961px;
    display: flex; flex-direction: column;
    align-items: center; justify-content: center; gap: 60px;
  }
  .card {
    position: relative;
    width: 700px; height: 400px;
    overflow: hidden;
    box-shadow: 0 6px 18px rgba(0,0,0,.18);
  }
  .card--front { background: var(--paper); }
  .card--back { background: var(--brand-blue); display: flex; align-items: center; justify-content: center; }

  .card__swoosh { position: absolute; inset: 0; width: 700px; height: 400px; }
  .swoosh-edge { fill: var(--deep-blue); }
  .swoosh-gap { fill: var(--paper); }
  .swoosh-field { fill: var(--brand-blue); }

  .holder {
    position: absolute; top: 28px; right: 50px;
    text-align: center; color: var(--paper);
    font-family: "Tinos", "Times New Roman", serif;
  }
  .holder__name { font-weight: 700; font-size: 27px; line-height: 1.1; }
  .holder__title { font-size: 19px; line-height: 1.2; }

  .firm-name {
    display: flex; align-items: center; gap: 14px;
    font-family: "Tinos", "Times New Roman", serif;
    font-weight: 700; font-size: 44px; line-height: 1;
    color: var(--brand-blue);
    white-space: nowrap;
  }
  .firm-name__square { width: 14px; height: 14px; background: currentColor; flex: none; }
  .card--front .firm-name { position: absolute; left: 44px; top: 170px; }
  .card--back .firm-name { color: var(--paper); font-size: 64px; gap: 18px; }
  .card--back .firm-name__square { width: 18px; height: 18px; }

  .contact {
    position: absolute; left: 44px; bottom: 40px;
    list-style: none;
    font-family: "Tinos", "Times New Roman", serif;
    font-size: 16.5px; color: var(--ink);
  }
  .contact__item { display: flex; align-items: center; gap: 12px; height: 30px; }
  .contact__icon { width: 16px; height: 16px; fill: var(--ink); flex: none; }

  .divider {
    position: absolute; left: 430px; bottom: 40px;
    width: 1px; height: 82px; background: var(--rule);
  }
  .tagline {
    position: absolute; left: 450px; right: 30px; bottom: 62px;
    font-family: "Tinos", "Times New Roman", serif;
    font-weight: 700; font-size: 17px; letter-spacing: 1px;
    color: var(--ink); text-align: center; line-height: 1.3;
  }
</style>
</head>
<body>
<main class="stage">

  <section class="card card--front" aria-label="Business card front">
    <svg class="card__swoosh" viewBox="0 0 700 400" aria-hidden="true">
      <path class="swoosh-edge" d="M0,0 H700 V342 C640,160 420,64 0,64 Z"/>
      <path class="swoosh-gap" d="M0,0 H700 V330 C638,152 420,57 0,57 Z"/>
      <path class="swoosh-field" d="M0,0 H700 V318 C634,144 420,50 0,50 Z"/>
    </svg>

    <div class="holder">
      <p class="holder__name">Tobias Marlow</p>
      <p class="holder__title">Attorney</p>
    </div>

    <p class="firm-name"><span class="firm-name__square"></span>Brinmoor Legal</p>

    <ul class="contact">
      <li class="contact__item">
        <svg class="contact__icon" viewBox="0 0 24 24" aria-hidden="true"><path d="M6.6 10.8a15.2 15.2 0 0 0 6.6 6.6l2.2-2.2a1 1 0 0 1 1-.25 11.4 11.4 0 0 0 3.6.57 1 1 0 0 1 1 1V20a1 1 0 0 1-1 1A17 17 0 0 1 3 4a1 1 0 0 1 1-1h3.5a1 1 0 0 1 1 1c0 1.250.2 2.450.57 3.57a1 1 0 0 1-.25 1z"/></svg>
        <span>855-FIRM-ONE (347-6663)</span>
      </li>
      <li class="contact__item">
        <svg class="contact__icon" viewBox="0 0 24 24" aria-hidden="true"><path d="M3 5h18a1 1 0 0 1 1 1v12a1 1 0 0 1-1 1H3a1 1 0 0 1-1-1V6a1 1 0 0 1 1-1zm1 2.2V17h16V7.2l-8 5.3z"/></svg>
        <span>tobias.marlow@brinmoorlegal.com</span>
      </li>
      <li class="contact__item">
        <svg class="contact__icon" viewBox="0 0 24 24" aria-hidden="true"><path d="M12 2a10 10 0 1 0 0 20 10 10 0 0 0 0-20zm-1 2.1V11H6.05A8 8 0 0 1 11 4.1zm2 0A8 8 0 0 1 17.95 11H13zM4.06 13H11v6.9A8 8 0 0 1 4.06 13zM13 13h6.94A8 8 0 0 1 13 19.9z"/></svg>
        <span>www.brinmoorlegal.com</span>
      </li>
    </ul>

    <div class="divider"></div>
    <p class="tagline">A Law Firm For Service<br>Members And Veterans</p>
  </section>

  <section class="card card--back" aria-label="Business card back">
    <p class="firm-name"><span class="firm-name__square"></span>Brinmoor Legal</p>
  </section>

</main>
</body>
</html>
```